Wine Shop Banners

Banner graphic/images required
Require banner images to match the present online wine shop.

www.korbel-tafelhaus.de

The wine-shop presently has a very clean, simple design, lots of white space, which is very much the trend at the moment.

Requirements
Images or graphic design for present banners visible on the homepage

The colour and feeling of the banners must fit in with the present clean, simple design.

Work required
3 large slide-card/banners (can be more) and 3 smaller fixed banners below. Please view website to see present position of banners.

LARGE BANNERS x 3

Something special with white background within the banner space
White background on each slide-card. Small individual graphic image in the middle of the slide card. This could be either a simple element of wine:
ingredients, fruit (grape), bottle, cork, old bottle label etc. just displaying one item on each slide-card. Preferably with high quality graphic features.

Note:
We are trying the steer away from the classic stereotype wineshop design. The image/s should have a higher, individual graphic touch, which gives the design something different. Sometimes such artistic work is displayed in steampunk or even in nostalgic design, which leaves the viewer slightly memorized with the content.
To clarify: we are not looking for a full steampunk design but possibly certain elements of this will give you an idea what we mean. That is to say, the design can go slightly in this direction without going over the top. Something small but very eye-catching.

SMALLER BANNERS x 3

One idea is:
Showing a symbol e.g. - discount sign "%" against a white background but again with a high graphic quality.

Target Market(s)

People interested in purchasing wine.
Ages approx. 25 to 65

Industry/Entity Type

Shop

Requirements
Must have
• Something special with white background
• Small individual graphic image in the middle of the slide card.
Nice to have
• The image/s should have a higher, individual graphic touch, which gives the design something different. Something that leaves the viewer slightly memorized with the content.
Should not have
• Not the typical classical design that is often seen on wine shops.

```html
<!DOCTYPE html>
<html lang="en">
<head>
<meta charset="utf-8">
<title>Royal Quality Wine – Banner</title>
<link rel="stylesheet" href="https://fonts.googleapis.com/css2?family=Cinzel:wght@400&family=Marcellus&display=swap">
<style>
  :root {
    --page-bg: #e6e8e2;
    --banner-bg: #ffffff;
    --tagline: #9c2a4c;
    --headline: #545b2f;
    --subline: #4d4f3a;
    --vineyard-light: #f6f6f3;
    --vineyard-mid: #ecece7;
    --panel-dark: #111111;
    --panel-light: #3a3a3a;
    --bottle-dark: #0c0d0c;
    --bottle-light: #2b302c;
  }
  * { margin: 0; padding: 0; box-sizing: border-box; }
  html, body {
    width: 1200px;
    height: 649px;
    overflow: hidden;
    background: var(--page-bg);
  }
  .banner {
    position: absolute;
    left: 0;
    top: 91px;
    width: 1200px;
    height: 467px;
    background: var(--banner-bg);
    overflow: hidden;
  }
  .vineyard-art {
    position: absolute;
    left: 340px;
    top: 0;
    width: 740px;
    height: 467px;
    background:
      radial-gradient(ellipse 60% 55% at 55% 55%, var(--vineyard-mid) 0%, var(--vineyard-light) 60%, rgba(255,255,255,0) 100%);
  }
  .dark-panel {
    position: absolute;
    left: 965px;
    top: 0;
    width: 235px;
    height: 467px;
    background: linear-gradient(160deg, var(--panel-light) 0%, var(--panel-dark) 45%, var(--panel-dark) 100%);
  }
  .bottle {
    position: absolute;
    left: 884px;
    top: 43px;
    width: 157px;
    height: 424px;
    border-radius: 20px 20px 0 0;
    background: linear-gradient(90deg, var(--bottle-light) 0%, var(--bottle-dark) 35%, var(--bottle-dark) 75%, var(--bottle-light) 100%);
  }
  .copy {
    position: absolute;
    left: 72px;
    top: 120px;
  }
  .tagline {
    font-family: "Cinzel", serif;
    font-size: 24px;
    line-height: 28px;
    letter-spacing: 0.5px;
    color: var(--tagline);
    white-space: nowrap;
  }
  .headline {
    font-family: "Cinzel", serif;
    font-weight: 400;
    font-size: 76px;
    line-height: 68px;
    letter-spacing: 1px;
    color: var(--headline);
    margin-left: -6px;
    margin-top: 4px;
  }
  .subline {
    font-family: "Marcellus", serif;
    font-size: 19px;
    line-height: 24px;
    color: var(--subline);
    margin-top: 26px;
    margin-left: 2px;
  }
</style>
</head>
<body>
  <section class="banner">
    <div class="vineyard-art" role="img" aria-label="Faint engraved drawing of a vineyard with a hilltop village"></div>
    <div class="dark-panel"></div>
    <div class="bottle" role="img" aria-label="Dark glass wine bottle"></div>
    <div class="copy">
      <p class="tagline">LOREM IPSUM DOLOR SIT AMET, CONSECTETUR</p>
      <h1 class="headline">ROYAL QUALITY<br>WINE</h1>
      <p class="subline">Surprise of&nbsp; Wine Gifts for Someone Special</p>
    </div>
  </section>
</body>
</html>
```